Local fast-growing company in the service sector

We are looking for a modern business card design, which should also appear on our letterheads

Target Market(s)

Private and industrial sectors

Contact Information for Business Card

Vorname Name
Kellberger Str. 18
74523 Lindenbach
Tel.: 07146-839214-0
Name@agentur-kvtl.de

Colors
9d9d9d
919191
aaaaaa

Requirements
Must have
• The logo (file) in silver

```html
<!DOCTYPE html>
<html lang="de">
<head>
<meta charset="utf-8">
<title>KVTL – Visitenkarte</title>
<link href="https://fonts.googleapis.com/css2?family=PT+Sans:wght@400;700&display=swap" rel="stylesheet">
<style>
  :root {
    --stage: #1a1a1a;
    --card-front: #58595b;
    --card-back: #5d5e60;
    --silver: #d2d2d2;
    --silver-soft: #aaaaaa;
    --silver-faint: #686a6c;
    --text: #e4e4e4;
  }
  * { margin: 0; padding: 0; box-sizing: border-box; }
  html, body { width: 1200px; height: 900px; overflow: hidden; }
  body {
    background: var(--stage);
    font-family: "PT Sans", "Myriad Pro", sans-serif;
    position: relative;
  }
  .card {
    position: absolute;
    top: 170px;
    width: 347px;
    height: 561px;
    overflow: hidden;
  }
  .card--front { left: 259px; background: var(--card-front); }
  .card--back { left: 631px; background: var(--card-back); }

  .front-mark {
    position: absolute;
    top: 150px;
    left: 0; right: 0;
    text-align: center;
    font-size: 92px;
    font-weight: 700;
    letter-spacing: 4px;
    color: var(--silver);
    line-height: 1;
  }
  .person-name {
    position: absolute;
    top: 358px;
    left: 0; right: 0;
    text-align: center;
    font-size: 19px;
    font-weight: 700;
    color: var(--text);
    letter-spacing: 0.3px;
  }
  .contact-icons {
    position: absolute;
    top: 402px;
    left: 0; right: 0;
    display: flex;
    justify-content: center;
    gap: 6px;
  }
  .contact-icons svg { width: 20px; height: 16px; fill: var(--text); }
  .contact-lines {
    position: absolute;
    top: 430px;
    left: 0; right: 0;
    text-align: center;
    font-size: 15.5px;
    line-height: 20.5px;
    color: var(--text);
  }
  .address {
    position: absolute;
    top: 504px;
    left: 0; right: 0;
    text-align: center;
    font-size: 15.5px;
    color: var(--text);
  }

  .back-watermark {
    position: absolute;
    top: 150px;
    left: 0; right: 0;
    text-align: center;
    font-size: 128px;
    font-weight: 700;
    color: var(--silver-faint);
    line-height: 1;
    letter-spacing: 4px;
  }
  .back-brand {
    position: absolute;
    top: 430px;
    left: 36px;
    display: flex;
    align-items: center;
    gap: 14px;
  }
  .back-brand__square {
    width: 62px;
    height: 62px;
    background: var(--silver-soft);
  }
  .back-brand__name {
    font-size: 64px;
    font-weight: 700;
    color: var(--silver-soft);
    letter-spacing: 3px;
    line-height: 1;
  }
</style>
</head>
<body>
  <section class="card card--front" aria-label="Visitenkarte Vorderseite">
    <div class="front-mark">KVTL</div>
    <p class="person-name">VORNAME NAME</p>
    <div class="contact-icons" aria-hidden="true">
      <svg viewBox="0 0 20 16"><path d="M5 1c1 0 2 2.5 2 3.3 0 .8-1.3 1.2-1.1 2 .5 1.7 2 3.2 3.7 3.7.8.2 1.2-1.1 2-1.1.8 0 3.3 1 3.3 2 0 1.5-1.5 3-3.3 3C6.3 13.9 2 9.6 2 4.3 2 2.5 3.5 1 5 1z"/></svg>
      <svg viewBox="0 0 20 16"><path d="M1 3h18v11H1z M2.5 4.5 10 9.5l7.5-5v-.1h-15z" fill-rule="evenodd"/></svg>
      <svg viewBox="0 0 20 16"><circle cx="10" cy="8" r="7"/><path d="M6 4c2 0 3 1 2.5 2.5S6 8 7 10s-1 3-1 3M13 3c-1 1.5 0 2.5 1.5 3s1.5 2 .5 3.5" stroke="#58595b" stroke-width="1.3" fill="none"/></svg>
    </div>
    <div class="contact-lines">
      <p>07146-839214-0</p>
      <p>Name@agentur-kvtl.de</p>
      <p>www.agentur-kvtl.de</p>
    </div>
    <p class="address">Kellberger Str. 18 74523 Lindenbach</p>
  </section>

  <section class="card card--back" aria-label="Visitenkarte Rückseite">
    <div class="back-watermark" aria-hidden="true">KVTL</div>
    <div class="back-brand">
      <span class="back-brand__square" aria-hidden="true"></span>
      <span class="back-brand__name">KVTL</span>
    </div>
  </section>
</body>
</html>
```